BLS Business Card 2018

Larkmere Chiropractic. We have two locations that we want to advertise on the same card. Brightvale OrthoCore campus address: 3815 Pellham Dr., Suite 240, Flowood, MS 39417. Madison address: 246 Willowmere Dr., Building D., Madison, MS 39284. website: www.drlarkmere-example.com. o:(601)555-0147 f:(601)555-0183

Target Market(s)

Health care decision makers: primary care doctors and mothers

Contact Information for Business Card

I have no idea; up for any suggestions and I'd do much better picking from examples versus describing what I'm looking for. We are in a very high end location and would like the cards to look really sharp.

Requirements
Must have
• My name, Martin R Belvane, D.C.

```html
<!DOCTYPE html>
<html lang="en">
<head>
<meta charset="utf-8">
<title>Larkmere Chiropractic – Business Card</title>
<link href="https://fonts.googleapis.com/css2?family=Cinzel:wght@400&family=Open+Sans:wght@400;700&display=swap" rel="stylesheet">
<style>
  :root {
    --stage: #ecebe8;
    --ink: #000000;
    --paper: #ffffff;
    --panel-grey: #333333;
    --figure-light: #f4f4f4;
    --figure-dark: #5a5a5a;
    --text-dark: #111111;
  }
  html, body {
    margin: 0;
    width: 1200px;
    height: 900px;
    overflow: hidden;
    background: var(--stage);
  }
  .canvas { position: relative; width: 1200px; height: 900px; }
  .card {
    position: absolute;
    width: 610px;
    height: 365px;
    overflow: hidden;
    box-shadow: 0 6px 18px rgba(0,0,0,0.18);
  }
  /* Front */
  .card-front { left: 175px; top: 52px; background: var(--ink); color: var(--paper); }
  .front-grey-band { position: absolute; right: 0; top: 0; width: 90px; height: 100%; background: var(--panel-grey); }
  .front-figure {
    position: absolute; left: 275px; top: 0; width: 335px; height: 365px;
    background: linear-gradient(160deg, var(--figure-light) 0%, #d8d8d8 45%, var(--figure-dark) 100%);
    clip-path: polygon(30% 10%, 62% 0, 100% 0, 100% 100%, 0 100%, 18% 60%);
  }
  .brand { position: absolute; display: flex; align-items: center; font-family: 'Cinzel', serif; font-weight: 400; }
  .brand-mark { border-radius: 50%; flex: none; }
  .brand-name { line-height: 1; }
  .brand-name span { display: block; }
  .front-brand { left: 40px; top: 88px; }
  .front-brand .brand-mark { width: 52px; height: 52px; border: 0; background: var(--paper); margin-right: 18px; }
  .front-brand .brand-primary { font-size: 32px; }
  .front-brand .brand-secondary { font-size: 20px; margin-top: 3px; }
  .doctor-name {
    position: absolute; left: 43px; top: 182px; margin: 0;
    font-family: 'Cinzel', serif; font-weight: 400; font-size: 19px; letter-spacing: 0.5px;
  }
  .contact-list {
    position: absolute; left: 43px; top: 226px; margin: 0; padding: 0; list-style: none;
    font-family: 'Open Sans', sans-serif; font-size: 15px; line-height: 21px;
  }
  /* Back */
  .card-back { left: 542px; top: 477px; background: var(--paper); color: var(--text-dark); }
  .back-brand { left: 100px; top: 88px; }
  .back-brand .brand-mark { width: 76px; height: 76px; background: var(--ink); margin-right: 24px; }
  .back-brand .brand-primary { font-size: 46px; }
  .back-brand .brand-secondary { font-size: 28px; margin-top: 2px; }
  .locations {
    position: absolute; left: 0; top: 226px; width: 100%; text-align: center;
    font-family: 'Open Sans', sans-serif; font-size: 15.5px; line-height: 21px;
  }
  .location { margin: 0 0 11px; }
  .location-name { display: block; font-weight: 700; font-size: 16px; }
</style>
</head>
<body>
<main class="canvas">
  <section class="card card-front">
    <div class="front-grey-band"></div>
    <div class="front-figure" role="img" aria-label="White silhouette illustration of a muscular figure seen from behind, arm raised"></div>
    <div class="brand front-brand">
      <span class="brand-mark"></span>
      <div class="brand-name"><span class="brand-primary">LARKMERE</span><span class="brand-secondary">CHIROPRACTIC</span></div>
    </div>
    <h1 class="doctor-name">MARTIN R BELVANE, D.C.</h1>
    <ul class="contact-list">
      <li>P: (601)555-0147</li>
      <li>F: (601)555-0183</li>
      <li>www.drlarkmere-example.com</li>
    </ul>
  </section>

  <section class="card card-back">
    <div class="brand back-brand">
      <span class="brand-mark"></span>
      <div class="brand-name"><span class="brand-primary">LARKMERE</span><span class="brand-secondary">CHIROPRACTIC</span></div>
    </div>
    <div class="locations">
      <p class="location"><span class="location-name">BRIGHTVALE ORTHOCORE CAMPUS</span>3815 Pellham Dr., Suite 240 Flowood, MS 39417.</p>
      <p class="location"><span class="location-name">MADISON</span>246 Willowmere Dr., Building D., Madison, MS 39284.</p>
    </div>
  </section>
</main>
</body>
</html>
```